Business Cards for IT Consulting Company (Managed Service Provider)

I am looking to have some business cards printed and would like some designs. We are an IT Consulting company based in Vancouver BC. I would like a nice clean and modern look to the cards. I have uploaded all the versions of my logo so parts can be used as needed. Here is a snippit from our website homepage:

Quillbrook Networks Ltd. is an IT Solutions Partner located in Vancouver BC, Canada. We offer IT solutions and support to customers in the greater Vancouver Area. With expertise in Microsoft platforms, as well as Linux and Mac OSX and over 12 years experience in the IT industry, Quillbrook Networks is dedicated to offering our clients top quality service and products. We take pride in the solutions we offer our customers. The greatest compliment a client can give us is to recommend our services.

Quillbrook Networks Ltd. offers a wide range of IT services from onsite service to remote support and managed service solutions. This allows clients to choose the support path that best suits their company’s needs. Supporting many different sized companies from small to enterprise level over the past 12 years Quillbrook Networks has the experience and expertise needed to ensure things run smoothly. Allowing our clients to focus on doing business.

Revolutionizing the way IT services are delivered.

Quillbrook Networks is dedicated to providing our clients with IT solutions that work and grow with them for years to come. This philosophy helps save money in the long run instead of replacing equipment constantly. Far too often IT solutions are not well thought out and while possibly solving the problem at hand, require replacement due to growth or quality within a very short time frame. Quillbrook Networks takes pride in providing solutions that will last and be able to accommodate growth without the need for replacement.

Industry/Entity Type

Information Technology

Contact Information for Business Card

Quillbrook Networks Ltd.
(Employee Name)
Eml: (Employees Email Address)
Web: quillbrook.me
Ph: 604-555-0148

Font styles to use
Serif
Sans Serif

Requirements
Must have
• The Company logo and company colors.
Nice to have
• - Our tag line: "Revolutionizing IT Services" or "Revolutionizing the way IT services are delivered."
• - Also I really like the idea of nature and technology together blending which is sort of where my logo came from so integrating that somehow onto the business cards would be great.

```html
<!DOCTYPE html>
<html lang="en">
<head>
<meta charset="UTF-8">
<title>Quillbrook Networks Ltd. – Business Cards</title>
<link href="https://fonts.googleapis.com/css2?family=Montserrat:wght@400;500;600;700&display=swap" rel="stylesheet">
<style>
  :root {
    --bg: #2b2b2d;
    --slate: #5f6062;
    --slate-dark: #4f5052;
    --brand-blue: #00aeef;
    --paper: #ffffff;
    --ink-soft: #6d6e70;
  }
  * { box-sizing: border-box; margin: 0; padding: 0; }
  html, body { width: 1200px; height: 900px; overflow: hidden; }
  body {
    background: var(--bg);
    font-family: 'Montserrat', sans-serif;
    position: relative;
  }
  .card {
    position: absolute;
    left: 280px;
    width: 640px;
    height: 366px;
    overflow: hidden;
    box-shadow: 0 14px 30px rgba(0,0,0,0.45);
  }

  /* Back of card */
  .card-back { top: 62px; background: var(--slate); }
  .back-wordmark {
    position: absolute;
    left: 0; right: 0; top: 118px;
    text-align: center;
    color: var(--brand-blue);
    font-weight: 600;
    font-size: 40px;
    letter-spacing: 0.5px;
  }
  .back-tagline-row {
    position: absolute;
    left: 0; right: 0; top: 272px;
    display: flex;
    align-items: center;
  }
  .back-rule { flex: 1; height: 1.5px; background: var(--brand-blue); }
  .back-tagline {
    color: var(--paper);
    font-size: 17px;
    font-weight: 500;
    letter-spacing: 1px;
    padding: 0 14px;
  }

  /* Front of card */
  .card-front { top: 472px; background: var(--paper); }
  .side-band {
    position: absolute;
    left: 44px; top: 0; bottom: 0;
    width: 96px;
    background: var(--slate);
  }
  .brand-lockup {
    position: absolute;
    left: 92px; top: 78px;
    display: flex;
    align-items: center;
    gap: 18px;
  }
  .brand-square { width: 70px; height: 70px; background: var(--brand-blue); }
  .brand-name {
    color: var(--brand-blue);
    font-weight: 600;
    line-height: 1;
  }
  .brand-name .primary { display: block; font-size: 54px; letter-spacing: -0.5px; }
  .brand-name .secondary { display: block; font-size: 20px; letter-spacing: 2px; margin-top: 4px; text-transform: uppercase; }

  .divider-line {
    position: absolute;
    left: 170px; right: 0; top: 200px;
    height: 4px;
    background: var(--slate);
  }
  .contact-panel {
    position: absolute;
    left: 170px; right: 0; top: 210px; bottom: 0;
    background: var(--brand-blue);
  }
  .person {
    position: absolute;
    right: 34px; top: 18px;
    text-align: right;
  }
  .person-name {
    color: var(--paper);
    font-weight: 700;
    font-size: 24px;
    letter-spacing: 1.5px;
  }
  .person-rule { height: 1px; background: var(--paper); width: 240px; margin: 4px 0 3px auto; }
  .person-title {
    color: var(--slate-dark);
    font-size: 12px;
    font-weight: 500;
    letter-spacing: 2px;
  }
  .contact-list {
    position: absolute;
    left: 40px; top: 72px;
    list-style: none;
    border-top: 1px solid var(--paper);
    padding-top: 8px;
    width: 250px;
  }
  .contact-item {
    display: flex;
    align-items: center;
    gap: 10px;
    color: var(--paper);
    font-size: 15px;
    font-weight: 500;
    letter-spacing: 0.5px;
    line-height: 22px;
  }
  .contact-icon { width: 12px; height: 12px; flex: none; }
</style>
</head>
<body>

  <section class="card card-back" aria-label="Business card back">
    <div class="back-wordmark">Quillbrook Networks</div>
    <div class="back-tagline-row">
      <span class="back-rule"></span>
      <span class="back-tagline">Revolutionizing IT Services</span>
      <span class="back-rule"></span>
    </div>
  </section>

  <section class="card card-front" aria-label="Business card front">
    <div class="side-band"></div>

    <div class="brand-lockup">
      <span class="brand-square"></span>
      <span class="brand-name">
        <span class="primary">Quillbrook</span>
        <span class="secondary">Networks Ltd.</span>
      </span>
    </div>

    <div class="divider-line"></div>

    <div class="contact-panel">
      <div class="person">
        <div class="person-name">DANIEL MARSH</div>
        <div class="person-rule"></div>
        <div class="person-title">DIRECTOR</div>
      </div>

      <ul class="contact-list">
        <li class="contact-item">
          <svg class="contact-icon" viewBox="0 0 24 24" aria-hidden="true"><path fill="#4f5052" d="M6.6 10.8a15.1 15.1 0 0 0 6.6 6.6l2.2-2.2c.3-.3.7-.4 1-.2 1.1.4 2.3.6 3.6.6.6 0 1 .4 1 1V20c0 .6-.4 1-1 1A17 17 0 0 1 3 4c0-.6.4-1 1-1h3.5c.6 0 1 .4 1 1 0 1.3.2 2.5.6 3.6.1.3 0 .7-.2 1z"/></svg>
          604-555-0148
        </li>
        <li class="contact-item">
          <svg class="contact-icon" viewBox="0 0 24 24" aria-hidden="true"><rect x="2" y="5" width="20" height="14" rx="1.5" fill="none" stroke="#4f5052" stroke-width="2.4"/><path d="M2.5 6l9.5 7 9.5-7" fill="none" stroke="#4f5052" stroke-width="2.4"/></svg>
          info@danielmarsh.com
        </li>
        <li class="contact-item">
          <svg class="contact-icon" viewBox="0 0 24 24" aria-hidden="true"><circle cx="12" cy="12" r="9.5" fill="none" stroke="#4f5052" stroke-width="2.4"/><path d="M2.5 12h19M12 2.5c3 3 3 16 0 19M12 2.5c-3 3-3 16 0 19" fill="none" stroke="#4f5052" stroke-width="2"/></svg>
          www.quillbrook.me
        </li>
      </ul>
    </div>
  </section>

</body>
</html>
```